Fire Risk Assessment App needs a sleek UI design

I need a sleek, modern but professional design for my 5 page Fire Risk Assessment App. Include gradient background, fire themed colours including reds, yellows, light orange and a touch of black. Design must ooze simplicity and professionalism. This is for the UK market. See attached images and word doc for more information.

Target Market(s)

General public and business owners

Industry/Entity Type

Technology / Fire Safety

Colors
00AB8E
00BBA5
67D7C9
C6EFE9
E9F9F6
59FF00
82FF00
B8FF75
E3FFCB
F4FFEA
FFC000
F8CF3A
FAE287
FDF2CF
FEFAEE
F0912C
F2A743
F7CA91
FBE8D2
FDF5EE
EE7325
F08F49
F5BC92
FAE3D3
FDF4ED
EB3D1F
EC4F4E
F09395
F8D3D4
FCEDEE

```html
<!DOCTYPE html>
<html lang="en">
<head>
<meta charset="utf-8">
<title>Fire Risk Assessment App – Screens</title>
<link href="https://fonts.googleapis.com/css2?family=Poppins:wght@400;500;600;700&family=Lato:wght@400;700&display=swap" rel="stylesheet">
<style>
:root{
  --canvas:#dcdcdc;
  --red:#eb3d1f;
  --red-bright:#e8261c;
  --orange:#f05a14;
  --orange-mid:#f0912c;
  --amber:#ffc000;
  --ink:#111111;
  --text:#333333;
  --muted:#9a9a9a;
  --white:#ffffff;
  --screen-top:#fdeee8;
  --screen-mid:#fdf5dc;
  --screen-low:#fdf3e4;
  --green:#20b14a;
}
*{margin:0;padding:0;box-sizing:border-box}
html,body{width:1200px;height:781px;overflow:hidden;background:var(--canvas)}
body{position:relative;font-family:"Lato",sans-serif;color:var(--text)}
.phone{position:absolute;top:61px;height:659px;border-radius:32px;overflow:hidden;
  background:linear-gradient(160deg,var(--screen-top) 0%,var(--screen-mid) 45%,var(--screen-low) 100%);
  box-shadow:0 6px 22px rgba(0,0,0,.08)}
.phone--welcome{left:73px;width:307px}
.phone--dashboard{left:448px;width:304px}
.phone--support{left:825px;width:303px}
.abs{position:absolute}
.headline{left:0;right:0;top:30px;text-align:center;font-family:"Poppins",sans-serif;font-weight:500;font-size:16.5px;line-height:27px;color:var(--ink)}
.headline .accent{color:var(--red-bright);font-weight:700}
.sheet{background:var(--white);border-radius:7px}
.sheet--back1{left:38px;top:125px;width:210px;height:250px;transform:rotate(-6deg);opacity:.75}
.sheet--back2{left:70px;top:112px;width:220px;height:255px;transform:rotate(6deg);opacity:.6}
.sheet--front{left:42px;top:109px;width:218px;height:268px;box-shadow:0 2px 10px rgba(0,0,0,.06)}
.sheet-peek{left:28px;font-size:9px;color:var(--ink);font-family:"Lato",sans-serif}
.q-head{left:19px;font-size:9.6px;line-height:17px;color:var(--ink);font-family:"Lato",sans-serif}
.radio{width:10px;height:10px;border:1.6px solid var(--amber);border-radius:50%}
.q-body{left:18px;font-size:8.7px;line-height:17px;color:var(--text)}
.answer-box{left:19px;top:188px;width:158px;height:24px;border:1px solid #d5d5d5;border-radius:3px;font-size:8.6px;text-align:center;line-height:22px;color:var(--text)}
.photo-btn{left:68px;top:233px;width:73px;height:35px;background:#e6e6e6;font-family:"Poppins",sans-serif;font-size:10.5px;text-align:center;line-height:35px;color:var(--ink)}
.label{left:16px;font-family:"Poppins",sans-serif;font-weight:500;font-size:11.6px;color:var(--ink)}
.field{left:16px;top:429px;width:275px;height:31px;background:var(--white);border-radius:3px;font-family:"Poppins",sans-serif;font-size:9.5px;color:#b5b5b5;line-height:31px;padding-left:10px}
.field svg{position:absolute;right:10px;top:8px}
.btn{background:linear-gradient(90deg,var(--orange) 0%,#f98b0e 70%,var(--amber) 100%);color:var(--white);font-family:"Poppins",sans-serif;font-weight:600;font-size:11.3px;border-radius:2px;display:flex;align-items:center;justify-content:center;gap:8px}
.or{left:190px;top:556px;font-family:"Poppins",sans-serif;font-size:8.5px;color:var(--text)}
.finger{left:205px;top:545px;width:33px;height:33px;background:var(--white);border-radius:3px}
.finger span{display:block;margin:6px;width:21px;height:21px;border-radius:50%;background:radial-gradient(circle,#555 0 20%,#ddd 22% 34%,#555 36% 48%,#ddd 50% 62%,#555 64% 76%,transparent 78%)}
.endorse{left:16px;top:597px;font-family:"Poppins",sans-serif;font-weight:500;font-size:13px;color:var(--orange)}
.topbar{left:0;top:0;width:100%;height:63px;background:linear-gradient(180deg,#ff5a00 0%,#ff7a00 60%,#ffb000 100%)}
.topbar-icon{left:14px;top:12px;width:38px;height:38px;border:2px solid var(--white);border-radius:50%;display:flex;align-items:center;justify-content:center}
.topbar-title{left:63px;top:20px;font-family:"Poppins",sans-serif;font-weight:600;font-size:15px;color:var(--white);letter-spacing:.2px}
.start{left:0;right:0;top:144px;text-align:center;font-family:"Poppins",sans-serif;font-size:10px;letter-spacing:.5px;color:var(--ink)}
.kind-icon{width:38px;height:38px;border-radius:50%;background:var(--white);border:1.5px solid var(--amber)}
.kind-icon span{display:block;margin:8px;width:19px;height:19px;border-radius:3px;background:linear-gradient(180deg,#b9c6d8,#6e86a8)}
.kind-label{font-family:"Poppins",sans-serif;font-size:12px;color:var(--ink);text-align:center;width:100px}
.status{left:14px;height:35px;background:var(--white);border:1px solid #f6b27a;box-shadow:0 1px 4px rgba(240,90,20,.18);display:flex;align-items:center;gap:8px;padding-left:10px;font-family:"Poppins",sans-serif;font-size:11.8px;color:var(--ink)}
.item{font-size:11.4px;color:var(--text);display:flex;align-items:center;gap:7px}
.dot{width:7px;height:7px;border-radius:50%;border:1.6px solid var(--amber)}
.dot--solid{background:var(--orange-mid);border-color:var(--orange-mid)}
.item--upper{font-family:"Poppins",sans-serif;font-size:11.4px;color:var(--ink)}
.mini-icon{width:26px;height:26px;border-radius:50%;background:var(--white);border:1.5px solid var(--amber)}
.mini-icon span{display:block;margin:5px;width:13px;height:13px;border-radius:2px;background:linear-gradient(180deg,#b9c6d8,#6e86a8)}
.navbar{left:0;bottom:0;width:100%;height:58px;background:var(--white)}
.nav-item{position:absolute;top:14px;width:26px;height:26px;transform:translateX(-13px)}
.reply{left:15px;top:92px;width:275px;height:145px;background:var(--white);border-radius:3px}
.reply-hint{left:15px;top:16px;font-size:11.4px;color:#999}
.reply svg{position:absolute;right:20px;top:14px}
</style>
</head>
<body>

<!-- Screen 1: welcome -->
<section class="phone phone--welcome">
  <h1 class="abs headline">The most user friendly’ <span class="accent">Fire Risk<br>Assessment App available</span></h1>

  <div class="abs sheet sheet--back1"></div>
  <div class="abs sheet sheet--back2"></div>
  <p class="abs sheet-peek" style="top:139px">FIR</p>
  <p class="abs sheet-peek" style="top:157px">HA</p>
  <p class="abs sheet-peek" style="top:177px">SE</p>

  <div class="abs sheet sheet--front">
    <p class="abs q-head" style="top:14px">FIRE RISK ASSESSMENT FIRE<br>HAZARDS</p>
    <span class="abs radio" style="left:182px;top:18px"></span>
    <p class="abs q-head" style="top:52px">SECTION 7-00/30-00</p>
    <span class="abs radio" style="left:182px;top:55px"></span>
    <svg class="abs" style="left:101px;top:78px" width="14" height="16" viewBox="0 0 14 16" role="img" aria-label="Flame symbol">
      <path d="M7 0C8 4 13 6 13 10.5A6 6 0 0 1 1 10.5C1 7.5 3 6 4 4C4.5 6 5.5 7 6.5 7C6 4 6 2 7 0Z" fill="#f04a1a"/>
      <path d="M7 8C8 10 10 11 10 12.5A3 3 0 0 1 4 12.5C4 11 6 10 7 8Z" fill="#ffc000"/>
    </svg>
    <p class="abs q-body" style="top:102px;font-size:9.2px;color:var(--ink)">Q: 7:01</p>
    <p class="abs q-body" style="top:119px">Are reasonable measures taken do<br>prevent fixes of electrical origin?</p>
    <svg class="abs" style="left:19px;top:161px" width="140" height="16" viewBox="0 0 140 16">
      <circle cx="8" cy="8" r="7" fill="#20b14a"/><path d="M4.5 8.2l2.3 2.3 4.5-4.8" stroke="#fff" stroke-width="1.8" fill="none"/>
      <circle cx="35" cy="8" r="7" fill="#e8261c"/><path d="M32.5 5.5l5 5M37.5 5.5l-5 5" stroke="#fff" stroke-width="1.6"/>
      <circle cx="62" cy="8" r="7" fill="#ffc000"/><path d="M58.5 8h7" stroke="#fff" stroke-width="1.8"/>
      <rect x="83" y="4" width="15" height="10" rx="1.5" fill="#777"/><rect x="87" y="2.5" width="6" height="2.5" fill="#777"/><circle cx="90.5" cy="9" r="2.8" fill="#fff"/>
      <circle cx="125" cy="8" r="7.5" fill="#1a2140"/><rect x="123" y="3.5" width="4" height="6.5" rx="2" fill="#fff"/><path d="M121.5 9a3.5 3.5 0 0 0 7 0M125 12.5v1.5" stroke="#fff" stroke-width="1" fill="none"/>
    </svg>
    <div class="abs answer-box">Lorem ipsum dolor sit amet</div>
    <div class="abs photo-btn">Photo</div>
  </div>

  <p class="abs label" style="top:400px">Quick tap responses and voice activated typing</p>
  <div class="abs field">Enter The Text Here
    <svg width="10" height="15" viewBox="0 0 10 15"><rect x="3" y="0.5" width="4" height="9" rx="2" fill="#c8c8c8"/><path d="M1 7a4 4 0 0 0 8 0M5 11v3M2.5 14h5" stroke="#c8c8c8" stroke-width="1.2" fill="none"/></svg>
  </div>
  <div class="abs btn" style="left:16px;top:473px;width:180px;height:31px">Create A Free Account
    <svg width="11" height="13" viewBox="0 0 11 13"><circle cx="5.5" cy="3.3" r="3.1" fill="#fff"/><path d="M0 13a5.5 5.5 0 0 1 11 0z" fill="#fff"/></svg>
  </div>
  <p class="abs label" style="top:517px">Any Responsible Person can do it</p>
  <div class="abs btn" style="left:16px;top:545px;width:144px;height:32px">Customer Log In
    <svg width="17" height="16" viewBox="0 0 17 16"><path d="M6 3.2A6.5 6.5 0 1 1 6 12.8" stroke="#fff" stroke-width="1.6" fill="none"/><path d="M1 8h9M7 5l3 3-3 3" stroke="#fff" stroke-width="1.6" fill="none"/></svg>
  </div>
  <p class="abs or">( OR )</p>
  <div class="abs finger" role="img" aria-label="Fingerprint login"><span></span></div>
  <p class="abs endorse">Create and endorsed by Fire Safety Experts</p>
</section>

<!-- Screen 2: dashboard -->
<section class="phone phone--dashboard">
  <header class="abs topbar">
    <div class="abs topbar-icon">
      <svg width="22" height="18" viewBox="0 0 22 18"><path d="M3 15A9 9 0 1 1 19 15" stroke="#fff" stroke-width="1.8" fill="none" stroke-linecap="round"/><path d="M11 11l4-5" stroke="#fff" stroke-width="1.8" stroke-linecap="round"/></svg>
    </div>
    <h2 class="abs topbar-title">DASHBOARD</h2>
  </header>

  <svg class="abs" style="left:0;top:80px" width="304" height="150" viewBox="0 0 304 150">
    <path d="M141 40L119 92M161 40L183 92" stroke="#555" stroke-dasharray="3 3" fill="none"/>
    <circle cx="151" cy="25" r="20" fill="#e8261c"/>
    <path d="M151 15v20M141 25h20" stroke="#fff" stroke-width="5"/>
  </svg>
  <p class="abs start">START FIRE RISK ASSESSMENT</p>
  <svg class="abs" style="left:60px;top:155px" width="190" height="20" viewBox="0 0 190 20">
    <path d="M30 0L20 18M150 0L160 18" stroke="#555" stroke-dasharray="3 3"/>
  </svg>
  <div class="abs kind-icon" style="left:70px;top:172px" role="img" aria-label="Commercial building icon"><span></span></div>
  <div class="abs kind-icon" style="left:194px;top:172px" role="img" aria-label="Residential house icon"><span style="background:linear-gradient(180deg,#6e86a8 0 40%,#e8e8e8 40%)"></span></div>
  <p class="abs kind-label" style="left:39px;top:217px">Commercial</p>
  <p class="abs kind-label" style="left:163px;top:217px">Residential</p>

  <div class="abs status" style="top:262px;width:118px">COMPLETE
    <svg width="14" height="14" viewBox="0 0 14 14"><circle cx="7" cy="7" r="7" fill="#20b14a"/><path d="M3.8 7.2l2.2 2.2 4.2-4.5" stroke="#fff" stroke-width="1.7" fill="none"/></svg>
  </div>
  <div class="abs item item--upper" style="left:15px;top:311px"><span class="dot dot--solid"></span>MILO'S BARBERSHOP
    <span class="mini-icon" role="img" aria-label="Commercial building icon"><span></span></span>
  </div>

  <div class="abs status" style="top:353px;width:134px">IN PROGRESS
    <svg width="18" height="18" viewBox="0 0 18 18"><circle cx="9" cy="9" r="7.5" stroke="#e6e6e6" stroke-width="2" fill="none"/><path d="M9 1.5A7.5 7.5 0 0 1 16.5 9" stroke="#20b14a" stroke-width="2" fill="none"/></svg>
  </div>
  <div class="abs item" style="left:15px;top:402px"><span class="dot"></span>Elm Rd School</div>
  <div class="abs item" style="left:132px;top:402px"><span class="dot"></span>St Anne's Nursing Home</div>

  <div class="abs status" style="top:439px;width:134px">PURCHASES
    <svg width="17" height="16" viewBox="0 0 17 16" style="margin-left:14px"><path d="M1 1h3l2 9h8l2-6H5" stroke="#333" stroke-width="1.6" fill="none"/><circle cx="7" cy="13.5" r="1.5" fill="#333"/><circle cx="13" cy="13.5" r="1.5" fill="#333"/></svg>
  </div>
  <div class="abs item" style="left:15px;top:486px"><span class="dot"></span>Residential Fire Risk Assessment</div>
  <div class="abs item" style="left:15px;top:513px"><span class="dot"></span>Commercial Fire Risk Assessment</div>
  <div class="abs item" style="left:15px;top:540px"><span class="dot"></span>Commercial Fire Risk Assessment</div>

  <nav class="abs navbar">
    <svg class="nav-item" style="left:52px" viewBox="0 0 26 26"><path d="M4 21A11 11 0 1 1 22 21" stroke="#f05a14" stroke-width="2.4" fill="none" stroke-linecap="round"/><path d="M13 15l4-6" stroke="#f05a14" stroke-width="2.2" stroke-linecap="round"/></svg>
    <svg class="nav-item" style="left:120px" viewBox="0 0 26 26"><path d="M3 5h4l3 11h10l3-8H8" stroke="#aaa" stroke-width="2" fill="none"/><circle cx="11" cy="21" r="2" fill="#aaa"/><circle cx="19" cy="21" r="2" fill="#aaa"/></svg>
    <svg class="nav-item" style="left:186px" viewBox="0 0 26 26"><circle cx="11" cy="11" r="8" fill="#aaa"/><path d="M17 13a7 7 0 1 1-3 8l-4 2 2-4" fill="#c8c8c8"/></svg>
    <svg class="nav-item" style="left:252px" viewBox="0 0 26 26"><circle cx="16" cy="4" r="2.5" fill="#aaa"/><path d="M8 10l5-3 4 3 3 3M13 7l-2 8 5 4-1 6M11 15l-4 5H3" stroke="#aaa" stroke-width="2.2" fill="none" stroke-linecap="round"/></svg>
  </nav>
</section>

<!-- Screen 3: technical support -->
<section class="phone phone--support">
  <header class="abs topbar">
    <div class="abs topbar-icon">
      <svg width="22" height="20" viewBox="0 0 22 20"><circle cx="9" cy="8.5" r="7.5" fill="#fff"/><path d="M15 8a6 6 0 1 1-3 10l-4 1 2-3" fill="#fff" opacity=".8"/><text x="9" y="12" text-anchor="middle" font-family="Poppins,sans-serif" font-size="10" font-weight="700" fill="#ff6a00">?</text></svg>
    </div>
    <h2 class="abs topbar-title">TECHNICAL SUPPORT</h2>
  </header>

  <div class="abs reply">
    <p class="abs reply-hint">Type / record you response here</p>
    <svg width="10" height="15" viewBox="0 0 10 15"><rect x="3" y="0.5" width="4" height="9" rx="2" fill="#aaa"/><path d="M1 7a4 4 0 0 0 8 0M5 11v3M2.5 14h5" stroke="#aaa" stroke-width="1.2" fill="none"/></svg>
  </div>
  <div class="abs btn" style="left:15px;top:261px;width:86px;height:32px">Send
    <svg width="14" height="14" viewBox="0 0 14 14"><path d="M13 1L1 6l4 2 1 5 2-3 3 2z" fill="#fff"/></svg>
  </div>

  <nav class="abs navbar">
    <svg class="nav-item" style="left:53px" viewBox="0 0 26 26"><path d="M4 21A11 11 0 1 1 22 21" stroke="#aaa" stroke-width="2.4" fill="none" stroke-linecap="round"/><path d="M13 15l4-6" stroke="#aaa" stroke-width="2.2" stroke-linecap="round"/></svg>
    <svg class="nav-item" style="left:120px" viewBox="0 0 26 26"><path d="M3 5h4l3 11h10l3-8H8" stroke="#aaa" stroke-width="2" fill="none"/><circle cx="11" cy="21" r="2" fill="#aaa"/><circle cx="19" cy="21" r="2" fill="#aaa"/></svg>
    <svg class="nav-item" style="left:185px" viewBox="0 0 26 26"><circle cx="11" cy="11" r="8" fill="#f05a14"/><path d="M17 13a7 7 0 1 1-3 8l-4 2 2-4" fill="#ffc000"/><text x="11" y="15" text-anchor="middle" font-family="Poppins,sans-serif" font-size="11" font-weight="700" fill="#fff">?</text></svg>
    <svg class="nav-item" style="left:253px" viewBox="0 0 26 26"><circle cx="16" cy="4" r="2.5" fill="#aaa"/><path d="M8 10l5-3 4 3 3 3M13 7l-2 8 5 4-1 6M11 15l-4 5H3" stroke="#aaa" stroke-width="2.2" fill="none" stroke-linecap="round"/></svg>
  </nav>
</section>

</body>
</html>
```